Newsletter Ad

I am looking for someone to design an advertisement for a mother's club newsletter. 4" wide X by 5" tall (and 2.5" wide X 5" tall if possible).

I'm a psychotherapist, so want the ad to look professional, but modern. I have a logo with my photo attached that can be incorporated into the design. The colors of my website are turquoise and white. I'd like to keep with that theme...so maybe some turquoise blocking to match the logo font color.

I'm uploading a logo as well as an ad draft with the content I'd like listed in the ad.

```html
<!DOCTYPE html>
<html lang="en">
<head>
<meta charset="utf-8">
<title>Dana Morel, MA, MFT – Newsletter Ad</title>
<link href="https://fonts.googleapis.com/css2?family=Questrial&display=swap" rel="stylesheet">
<style>
  :root {
    --turquoise: #0bc9ca;
    --teal-ink: #2a9696;
    --ink: #2a2a2a;
    --white: #ffffff;
    --photo-dark: #2b2520;
    --photo-warm: #9a7a5c;
  }
  * { box-sizing: border-box; margin: 0; padding: 0; }
  html, body {
    width: 961px; height: 1200px; overflow: hidden; background: var(--white);
  }
  .ad {
    position: relative; width: 961px; height: 1200px;
    background: var(--white);
    font-family: "Questrial", "Helvetica Neue", Arial, sans-serif;
    color: var(--ink);
  }
  .portrait {
    position: absolute; left: 33px; top: 70px; width: 176px; height: 214px;
    background: linear-gradient(135deg, var(--photo-dark) 0%, var(--photo-warm) 55%, var(--photo-dark) 100%);
  }
  .name {
    position: absolute; left: 238px; top: 72px;
    font-size: 60px; font-weight: 400; letter-spacing: 0.5px;
    color: var(--teal-ink); white-space: nowrap;
  }
  .tagline {
    position: absolute; left: 230px; width: 590px; top: 192px;
    text-align: center; font-size: 35px; line-height: 47px; font-weight: 400;
  }
  .services-band {
    position: absolute; left: 0; top: 326px; width: 961px; height: 594px;
    background: var(--turquoise);
  }
  .services {
    list-style: none; position: absolute; left: 0; top: 51px; width: 961px;
    text-align: center; color: var(--white);
    font-size: 37px; line-height: 60.8px;
  }
  .contact {
    position: absolute; left: 0; top: 930px; width: 966px;
    text-align: center; font-size: 35px; line-height: 47.3px; font-style: normal;
  }
  .license-band {
    position: absolute; left: 0; top: 1125px; width: 961px; height: 75px;
    background: var(--turquoise);
  }
  .license {
    position: absolute; right: 22px; top: 14px;
    color: var(--white); font-size: 24px;
  }
</style>
</head>
<body>
<main class="ad">
  <div class="portrait" role="img" aria-label="Portrait photo of the therapist"></div>
  <h1 class="name">DANA MOREL, MA, MFT</h1>
  <p class="tagline">Psychotherapy for<br>Individuals, Couples and Families</p>

  <section class="services-band">
    <ul class="services">
      <li>Parenting</li>
      <li>Depression</li>
      <li>Anxiety</li>
      <li>Life Transitions</li>
      <li>Divorce</li>
      <li>Couples Issues</li>
      <li>Women’s Issues</li>
      <li>Attachment and Neuroscience</li>
    </ul>
  </section>

  <address class="contact">
    418 Alder Lane, Fernbrook, CA 94900<br>
    www.danamorel.com<br>
    dana@danamorel.com<br>
    415.555.0182
  </address>

  <footer class="license-band">
    <span class="license">License# MFC00000</span>
  </footer>
</main>
</body>
</html>
```